Mental Health Therapy Website

I need a design for a mental health therapy website. It is a private practice. The business name is Fenwick Counseling, PLLC. My name is Martin Fenwick, LMHC, NCC, DCC. I would like some of the features/menus to be Home; Welcome/About Me, Rates and Services, Common Questions, and Contact.
If possible I would like a blog on the main page that I can update with articles I write. I would like the contact page to feature a map to my location (4189 Birchmont Ave. S, Lakewood, WA 98312).
I would like to place a small photo of me on the Welcome/About page.
I am new to this so if I am forgetting anything, please ask me!!
I will upload my logo so you can fit it and the color scheme into the design.
Thank you so very much!

```html
<!DOCTYPE html>
<html lang="en">
<head>
<meta charset="utf-8">
<title>Fenwick Counseling, PLLC</title>
<link rel="stylesheet" href="https://fonts.googleapis.com/css2?family=Source+Sans+3:wght@400;600;700&display=swap">
<style>
  :root {
    --stripe-pink: #d9418c;
    --stripe-orange: #f29a2e;
    --stripe-yellow: #f4cf3a;
    --stripe-green: #7fbf4a;
    --stripe-blue: #3a8fd0;
    --brand-navy: #1f4f7c;
    --brand-mark: #5a9a3c;
    --header-bg: #ffffff;
    --toggle-border: #d6d6d6;
    --toggle-bar: #8a8a8a;
    --hero-deep: #24495f;
    --hero-mid: #5f8fa8;
    --hero-light: #a9c7d6;
    --service-blue: #2d93cd;
    --text-light: #ffffff;
  }
  * { box-sizing: border-box; margin: 0; padding: 0; }
  html, body {
    width: 1200px;
    height: 2400px;
    overflow: hidden;
    background: var(--service-blue);
    font-family: "Source Sans 3", sans-serif;
  }
  .site { width: 1200px; height: 2400px; display: flex; flex-direction: column; }

  .accent-stripe { display: flex; height: 14px; }
  .accent-stripe span { flex: 1; }
  .accent-stripe .pink { background: var(--stripe-pink); }
  .accent-stripe .orange { background: var(--stripe-orange); }
  .accent-stripe .yellow { background: var(--stripe-yellow); }
  .accent-stripe .green { background: var(--stripe-green); }
  .accent-stripe .blue { background: var(--stripe-blue); }

  .site-header {
    height: 277px;
    background: var(--header-bg);
    display: flex;
    align-items: center;
    justify-content: space-between;
    padding: 0 32px 0 20px;
  }
  .brand { display: flex; align-items: center; gap: 26px; }
  .brand-dot {
    width: 170px; height: 170px; border-radius: 50%;
    background: var(--brand-mark);
  }
  .brand-name {
    color: var(--brand-navy);
    font-weight: 600;
    font-size: 78px;
    line-height: 0.95;
  }
  .menu-toggle {
    width: 156px; height: 114px;
    border: 3px solid var(--toggle-border);
    border-radius: 14px;
    display: flex; flex-direction: column;
    justify-content: center; align-items: center; gap: 18px;
    background: var(--header-bg);
  }
  .menu-toggle span {
    width: 78px; height: 8px; border-radius: 4px;
    background: var(--toggle-bar);
  }

  .hero {
    position: relative;
    height: 1058px;
    display: flex; flex-direction: column;
    justify-content: center; align-items: center;
    text-align: center;
    color: var(--text-light);
    padding: 0 40px 120px;
  }
  .hero-photo {
    position: absolute; inset: 0;
    background: linear-gradient(150deg, var(--hero-deep) 0%, var(--hero-mid) 55%, var(--hero-light) 100%);
  }
  .hero-title, .hero-lead { position: relative; }
  .hero-title {
    font-weight: 700;
    font-size: 100px;
    line-height: 1.1;
    text-transform: uppercase;
    margin-bottom: 14px;
  }
  .hero-lead {
    font-weight: 400;
    font-size: 84px;
    line-height: 1.3;
  }

  .services {
    flex: 1;
    background: var(--service-blue);
    color: var(--text-light);
    text-align: center;
    padding: 112px 60px 0;
  }
  .service-icon { width: 142px; height: 142px; margin: 0 auto 36px; display: block; }
  .service-title {
    font-weight: 700;
    font-size: 96px;
    line-height: 1.1;
    margin-bottom: 30px;
  }
  .service-text {
    font-weight: 400;
    font-size: 54px;
    line-height: 1.5;
  }
</style>
</head>
<body>
<div class="site">
  <div class="accent-stripe">
    <span class="pink"></span><span class="orange"></span><span class="yellow"></span><span class="green"></span><span class="blue"></span>
  </div>

  <header class="site-header">
    <div class="brand">
      <div class="brand-dot"></div>
      <div class="brand-name">Fenwick<br>Counseling</div>
    </div>
    <div class="menu-toggle" aria-label="Menu">
      <span></span><span></span><span></span>
    </div>
  </header>

  <section class="hero">
    <div class="hero-photo" role="img" aria-label="Photo of a hand touching a tablet screen"></div>
    <h1 class="hero-title">Here is Martin Fenwick</h1>
    <p class="hero-lead">I am a trauma certified therapist that utilizes CBT+ to assist with trauma</p>
  </section>

  <section class="services">
    <svg class="service-icon" viewBox="0 0 100 100" aria-hidden="true">
      <g fill="none" stroke="#ffffff" stroke-width="13" stroke-linecap="butt">
        <path d="M18 46 A32 32 0 0 1 78 32"/>
        <path d="M82 54 A32 32 0 0 1 22 68"/>
      </g>
      <polygon points="88,12 90,44 60,38" fill="#ffffff"/>
      <polygon points="12,88 10,56 40,62" fill="#ffffff"/>
    </svg>
    <h2 class="service-title">PSYCHOEDUCATION</h2>
    <p class="service-text">Lorem ipsum dolor sit amet, consectetuer adipiscing elit, sed diam nonummy nibh</p>
  </section>
</div>
</body>
</html>
```